Design WordPress Website for Contractor App Website

I need a graphic design for a WordPress website for our SaaS called Velumar Software. Please design the landing (Home) page first, before designing other pages. You can design other pages if your landing page is selected.

The design should be modern with a startup feel. The link to the trelvano doc below provides more information. And the attached image has the logo and some screenshots you can use. Copy text from the competitor's site listed as placeholders text or use Lorem Ipsum where needed.

https://files.trelvanodocs.net/doc/7QpXrLm2ZkW9vTbN4cHsYd1FjA8gEo3UiR6nKwBq/view?mode=share

Target Market(s)

Contractors, painters, plumbers, handymen, electricians, carpenters, landscapers, roofers, home service business.

Industry/Entity Type

Home Improvement

Number of Pages Required

5+ page

Colors
ffc214
34a6d7
9bcb3c

Requirements
Must have
• Look, professionals
Pindle Shelf and Apdex Shelf download icons
Focused on contractors
Nice to have
• Section for video

```html
<!DOCTYPE html>
<html lang="en">
<head>
<meta charset="utf-8">
<title>Velumar Software – Home</title>
<link href="https://fonts.googleapis.com/css2?family=Quicksand:wght@500;600;700&family=Roboto:ital,wght@0,400;0,500;0,700;1,400&display=swap" rel="stylesheet">
<style>
:root{
  --blue:#1d5ea9;
  --blue-dark:#164f92;
  --blue-light:#2f7fd0;
  --orange:#f47c20;
  --orange-red:#ff4a1c;
  --green:#7cb82f;
  --ink:#2b2b2b;
  --text:#555a60;
  --grey-bg:#f4f5f8;
  --footer:#1e1e1f;
  --white:#fff;
}
*{box-sizing:border-box;margin:0;padding:0}
html,body{width:1200px;height:4890px;overflow:hidden}
body{position:relative;background:var(--white);font-family:"Roboto",Arial,sans-serif;color:var(--text)}
.abs{position:absolute}
.heading{font-family:"Quicksand",Arial,sans-serif;font-weight:700;color:var(--ink)}
.btn{position:absolute;display:flex;align-items:center;justify-content:center;border-radius:20px;color:#fff;font-family:"Quicksand",sans-serif;font-weight:700;font-size:16px;box-shadow:0 4px 8px rgba(0,0,0,.18)}
.btn-orange{background:linear-gradient(180deg,#ff8a3a,#f05a14)}
.btn-green{background:linear-gradient(180deg,#8fcc3c,#6aa925)}
.btn-blue{background:linear-gradient(180deg,#2f8df0,#1667c8)}

/* header */
.site-header{position:absolute;left:0;top:0;width:1200px;height:100px;z-index:3}
.brand{position:absolute;display:flex;align-items:center;gap:10px;font-family:"Quicksand",sans-serif;font-weight:700;letter-spacing:3px}
.brand-dot{width:46px;height:46px;border-radius:50%;background:var(--orange)}
.brand-name{font-size:30px;color:var(--blue)}
.nav a{position:absolute;top:40px;font-family:"Quicksand",sans-serif;font-weight:600;font-size:17px;color:var(--blue);text-decoration:none}
.nav a.active{color:var(--orange)}

/* hero */
.hero{position:absolute;left:0;top:0;width:1200px;height:700px;background:linear-gradient(170deg,#fff 0%,#eef1f5 45%,#f7f8fa 70%,#fff 100%);overflow:hidden}
.hero h1{position:absolute;left:175px;top:214px;font-size:41px;line-height:48px;color:var(--blue)}

/* laptop */
.laptop-screen{position:absolute;left:636px;top:194px;width:460px;height:300px;background:#1c1c1c;border-radius:14px 14px 0 0;padding:14px 14px 0}
.laptop-inner{width:100%;height:100%;background:#fff;overflow:hidden;position:relative}
.laptop-base{position:absolute;left:585px;top:494px;width:563px;height:22px;background:linear-gradient(180deg,#d8d9db,#9ea0a4);border-radius:0 0 40px 40px}
.app-bar{height:52px;background:var(--orange-red);color:#fff;font-family:"Roboto",sans-serif;font-size:20px;display:flex;align-items:center;padding-left:20px;gap:26px}
.field{position:absolute;border:1px solid #9a9a9a;border-radius:4px}
.field label{position:absolute;left:8px;top:-9px;background:#fff;padding:0 4px;font-size:12px;color:#666}

/* phone */
.phone{position:absolute;width:213px;height:438px;background:#111;border-radius:26px;padding:9px 8px 0;box-shadow:0 14px 24px rgba(0,0,0,.25)}
.phone-screen{width:197px;height:396px;background:#fff;border-radius:18px 18px 0 0;overflow:hidden;position:relative;font-size:9px;color:#333}
.phone-nav{height:33px;display:flex;align-items:center;justify-content:space-around;color:#fff;font-size:12px;padding:0 30px}
.est-bar{height:42px;background:var(--orange-red);color:#fff;font-size:11px;padding:14px 12px 0}
.tabs{display:flex;justify-content:space-between;padding:8px 6px;font-size:8px;color:#666;border-bottom:1px solid #ddd}
.tabs span:first-child{color:var(--orange-red)}
.est-row{position:relative;height:83px;border-bottom:1px solid #ddd;padding:10px 6px}
.est-row .name{font-weight:500;font-size:9px}
.est-row .id{margin-top:9px;font-size:8px;color:#777}
.est-row .ref{margin-top:9px;font-size:9px;font-weight:500}
.pill{position:absolute;right:6px;top:10px;border:1px solid #f07a6a;color:#e05a44;border-radius:8px;font-size:7px;padding:1px 7px}
.est-row .date{position:absolute;right:6px;top:31px;font-size:7px;color:#777}
.est-row .amt{position:absolute;right:6px;top:47px;font-size:9px;font-weight:700;color:#4aa02c}
.sort-row{position:absolute;left:0;bottom:8px;width:100%;display:flex;gap:8px;padding:0 6px}
.sort-row span{border-radius:14px;font-size:8px;padding:6px 10px;border:1px solid #ccc}
.sort-row span:first-child{background:#1e73e6;color:#fff;border-color:#1e73e6}
.fab{position:absolute;right:8px;bottom:50px;width:24px;height:24px;border-radius:50%;background:var(--orange-red);color:#fff;font-size:16px;line-height:24px;text-align:center}
.phone-sm{transform:scale(.76);transform-origin:0 0}

/* trades */
.trade{position:absolute;top:722px;width:175px;text-align:center}
.trade .photo{width:175px;height:175px;border-radius:50%}
.trade p{margin-top:18px;font-family:"Roboto",sans-serif;font-weight:500;font-size:17px;color:#333}
.chev{position:absolute;top:772px}

/* about */
.para{font-size:13px;line-height:22px;color:var(--text)}

/* features */
.features-band{position:absolute;left:0;top:1490px;width:1200px;height:840px}
.feat{position:absolute;width:320px;color:#fff}
.feat h3{font-family:"Quicksand",sans-serif;font-weight:700;font-size:21px}
.feat p{margin-top:10px;font-size:13px;line-height:18px;color:#e6eefa}
.feat.right{text-align:right}
.feat-icon{position:absolute;width:40px;height:40px}

/* manage */
.checklist{list-style:none;position:absolute;left:171px;top:2572px}
.checklist li{position:relative;padding-left:16px;font-size:13px;line-height:23.5px;color:#444}
.checklist li::before{content:"";position:absolute;left:2px;top:9px;width:6px;height:6px;border-radius:50%;background:var(--orange)}

/* video */
.video-photo{position:absolute;left:0;top:3027px;width:650px;height:445px;background:linear-gradient(135deg,#c7ccd3 0%,#6c7fa0 40%,#3e5a8a 60%,#d9dde2 100%)}
.video-panel{position:absolute;left:650px;top:3027px;width:550px;height:445px;background:var(--orange)}
.play{position:absolute;left:273px;top:3212px;width:76px;height:76px;border-radius:50%;background:var(--orange)}

/* testimonials */
.testimonials{position:absolute;left:0;top:3472px;width:1200px;height:440px;background:var(--grey-bg)}
.quote{position:absolute;top:3620px;width:278px;height:140px;background:#fff;padding:22px 26px;font-style:italic;font-size:12.5px;line-height:18px;color:#555;box-shadow:0 2px 8px rgba(0,0,0,.06)}
.quote::after{content:"";position:absolute;left:26px;bottom:-12px;border:12px solid transparent;border-bottom:0;border-top-color:#fff}
.author{position:absolute;top:3778px;display:flex;align-items:center;gap:12px;font-family:"Quicksand",sans-serif;font-weight:700;font-size:15px;color:var(--orange)}
.avatar{width:44px;height:44px;border-radius:50%;background:linear-gradient(135deg,#d9b9a3,#8a6c5a)}

/* form phone */
.form-field{position:absolute;left:6px;width:185px;height:22px;border:1px solid #aaa;border-radius:3px;font-size:8px;padding:6px 0 0 22px}
.form-field label{position:absolute;left:6px;top:-7px;background:#fff;padding:0 2px;font-size:6px;color:#777}
.form-field i{position:absolute;left:7px;top:6px;width:8px;height:8px;background:#444;border-radius:1px}

/* store badges */
.badge{position:absolute;top:4332px;height:30px;background:#000;border-radius:5px;color:#fff;display:flex;align-items:center;gap:6px;padding:0 8px;font-size:11px;font-weight:500}
.badge i{width:12px;height:12px;border-radius:2px;background:#fff}

/* footer */
.site-footer{position:absolute;left:0;top:4505px;width:1200px;height:385px;background:var(--footer);color:#e8e8e8}
.f-col{position:absolute;top:82px}
.f-col h4{font-family:"Quicksand",sans-serif;font-weight:700;font-size:17px;color:#fff;margin-bottom:14px}
.f-col a{display:block;font-size:13px;line-height:24px;color:#ddd;text-decoration:none}
.social{position:absolute;top:160px;left:194px;display:flex;gap:8px}
.social span{width:28px;height:28px;border:1.5px solid #ddd;border-radius:50%}
.f-bottom{position:absolute;left:0;top:330px;width:1200px;text-align:center;font-size:12.5px;color:#ddd;word-spacing:1px}
.f-bottom span{margin:0 8px}
</style>
</head>
<body>

<!-- HERO -->
<section class="hero">
  <svg class="abs" style="left:0;top:0" width="1200" height="700" viewBox="0 0 1200 700" aria-hidden="true">
    <path d="M0 330 C220 230 380 470 640 360 S1000 260 1200 380 L1200 700 L0 700Z" fill="#e9ecf1"/>
    <path d="M0 420 C260 330 420 560 700 450 S1020 360 1200 470 L1200 700 L0 700Z" fill="#f3f5f8"/>
    <path d="M0 380 C240 300 420 520 680 410 S1020 320 1200 430" fill="none" stroke="#dfe3ea" stroke-width="3"/>
    <path d="M0 90 C200 20 300 240 520 160" fill="none" stroke="#e3e7ed" stroke-width="40" opacity=".6"/>
  </svg>
  <h1 class="heading">Now's the time.<br>Powerful software.<br>Strong community.<br>Real value.</h1>

  <div class="laptop-screen">
    <div class="laptop-inner">
      <div class="app-bar"><span>&#8592;</span><span>Company Information</span></div>
      <div class="abs" style="left:4px;top:66px;font-weight:700;font-size:15px;color:var(--blue)">ADDRESS</div>
      <div class="abs" style="left:0;top:92px;width:100%;border-top:1px solid #ccc"></div>
      <div class="abs" style="left:216px;top:124px;font-size:18px;font-weight:700;color:#2a7fd6">&#9906; Search</div>
      <div class="field" style="left:4px;top:186px;width:300px;height:46px"><label>Address Line 1</label>
        <span class="abs" style="left:14px;top:12px;font-size:16px;color:#444">&#8962;&nbsp;&nbsp; 418 Fernwood Ave</span></div>
      <div class="field" style="left:4px;top:256px;width:300px;height:46px"><label>City</label></div>
    </div>
  </div>
  <div class="laptop-base"></div>

  <div class="phone phone-sm" style="left:963px;top:251px">
    <div class="phone-screen">
      <div class="est-bar">Estimates</div>
      <div class="tabs"><span>ALL</span><span>CLOSED</span><span>OPEN</span><span>DRAFT</span></div>
      <div class="est-row"><div class="name">Elin Harrow</div><div class="id">INV-00245</div><div class="ref">EST-1029</div><span class="pill">Closed</span><span class="date">Aug 30, 2021</span><span class="amt">$300.99</span></div>
      <div class="est-row"><div class="name">Tomas Pell</div><div class="id">&nbsp;</div><div class="ref">EST-2098</div><span class="pill">Rejected</span><span class="date">Aug 30, 2021</span><span class="amt">$1,306.99</span></div>
      <div class="est-row"><div class="name">Mira Cole</div><div class="id">&nbsp;</div><div class="ref">EST-24945</div><span class="pill">Draft</span><span class="date">Aug 30, 2021</span><span class="amt">$946.99</span></div>
      <div class="est-row" style="border:0"><div class="name">Lyle Quint</div></div>
      <span class="fab">+</span>
      <div class="sort-row"><span>Sort By Date</span><span>Sort By Client</span></div>
    </div>
    <div class="phone-nav"><span>&#9664;</span><span>&#9679;</span><span>&#9632;</span></div>
  </div>
</section>

<header class="site-header">
  <div class="brand" style="left:171px;top:28px"><span class="brand-dot"></span><span class="brand-name">VELUMAR</span></div>
  <nav class="nav">
    <a class="active" href="#" style="left:434px">Home</a>
    <a href="#" style="left:519px">Features</a>
    <a href="#" style="left:623px">Pricing</a>
    <a href="#" style="left:718px">Services</a>
    <a href="#" style="left:821px">Contact</a>
    <a href="#" style="left:924px">Blog</a>
  </nav>
  <span class="btn btn-orange" style="left:980px;top:36px;width:86px;height:32px">Login</span>
</header>

<!-- TRADES -->
<svg class="chev" style="left:66px" width="30" height="72" viewBox="0 0 30 72" aria-hidden="true"><path d="M26 2 L4 36 L26 70" fill="none" stroke="#aab3c0" stroke-width="2"/></svg>
<svg class="chev" style="left:1106px" width="30" height="72" viewBox="0 0 30 72" aria-hidden="true"><path d="M4 2 L26 36 L4 70" fill="none" stroke="#aab3c0" stroke-width="2"/></svg>
<div class="trade" style="left:126px"><div class="photo" role="img" aria-label="Contractor in a safety vest holding a clipboard" style="background:radial-gradient(circle at 50% 40%,#c9a17c,#d8d033 55%,#7f9a9c)"></div><p>Contractors</p></div>
<div class="trade" style="left:320px"><div class="photo" role="img" aria-label="Painter holding a paint roller" style="background:radial-gradient(circle at 50% 40%,#e4c09b,#f0e2b4 55%,#d9c24a)"></div><p>Painters</p></div>
<div class="trade" style="left:513px"><div class="photo" role="img" aria-label="Plumber fixing pipes under a sink" style="background:radial-gradient(circle at 50% 40%,#8a8e94,#d8dadd 55%,#5f6c7e)"></div><p>Plumbers</p></div>
<div class="trade" style="left:707px"><div class="photo" role="img" aria-label="Handyman cutting wood" style="background:radial-gradient(circle at 50% 40%,#b98a60,#7a5b45 55%,#d7c1a5)"></div><p>Handymen</p></div>
<div class="trade" style="left:902px"><div class="photo" role="img" aria-label="Electrician working on a ceiling light" style="background:radial-gradient(circle at 50% 35%,#f0b060,#8a4a25 55%,#2e2520)"></div><p>Electrician</p></div>

<!-- ABOUT -->
<div class="abs" role="img" aria-label="Circular collage of tools with a house and hammer emblem" style="left:171px;top:1067px;width:372px;height:372px;border-radius:50%;background:conic-gradient(#2f5a3a 0 25%,#2a4d8a 0 50%,#8a4a20 0 75%,#b35a2a 0);"></div>
<h2 class="heading abs" style="left:587px;top:1078px;font-size:50px">About Velumar</h2>
<p class="para abs" style="left:587px;top:1152px;width:430px">Lorem ipsum dolor sit amet, consectetur adipiscing elit, sed do eiusmod tempor incididunt ut labore et dolore magna aliqua. Ut enim ad minim veniam, quis nostrud exercitation ullamco laboris nisi ut aliquip ex ea commodo consequat. Duis aute irure dolor in reprehenLorem ipsum do lor sit amet, consectetur adipiscing elit, sed do eiusmod tempor incid idunt ut labore et dolore magna aliqua. Ut enim ad minim veniam, quis nostrud exercitation ullamco laboris nisi ut aliquip.</p>
<span class="btn btn-orange" style="left:587px;top:1324px;width:120px;height:38px">Read More</span>

<!-- FEATURES -->
<svg class="features-band" viewBox="0 0 1200 840" preserveAspectRatio="none" aria-hidden="true">
  <defs><linearGradient id="bandGrad" x1="0" y1="0" x2="1" y2="1"><stop offset="0" stop-color="#2366b3"/><stop offset="1" stop-color="#174f97"/></linearGradient></defs>
  <path d="M0 50 C180 -10 330 0 520 40 S880 110 1200 30 L1200 770 C1000 830 800 800 560 810 S200 820 0 790 Z" fill="url(#bandGrad)"/>
  <path d="M0 230 C250 120 420 320 700 230 S1000 170 1200 260" fill="none" stroke="#2a6fbd" stroke-width="50" opacity=".5"/>
</svg>
<h2 class="heading abs" style="left:0;top:1628px;width:1200px;text-align:center;color:#fff;font-size:48px">Our Features</h2>

<svg class="feat-icon" style="left:180px;top:1778px" viewBox="0 0 40 40" aria-hidden="true"><circle cx="20" cy="20" r="16" fill="none" stroke="#fff" stroke-width="3"/><path d="M20 10 V20 L27 25" stroke="#fff" stroke-width="3" fill="none"/></svg>
<div class="feat" style="left:234px;top:1770px"><h3>Lorem ipsumolor</h3><p>Lorem ipsum dolor sit amet, cons ecteturdi piscing elit,sed do eiusm od tempororemum dolor sit.</p></div>
<svg class="feat-icon" style="left:180px;top:1914px" viewBox="0 0 40 40" aria-hidden="true"><circle cx="17" cy="11" r="8" fill="#fff"/><path d="M3 36 C3 22 31 22 31 36Z" fill="#fff"/><circle cx="31" cy="30" r="6" fill="var(--blue)" stroke="#fff" stroke-width="2"/></svg>
<div class="feat" style="left:234px;top:1908px"><h3>Lorem ipsumolor</h3><p>Lorem ipsum dolor sit amet, cons ecteturdi piscing elit,sed do eiusm od tempororemum dolor sit.</p></div>
<svg class="feat-icon" style="left:180px;top:2050px" viewBox="0 0 40 40" aria-hidden="true"><circle cx="16" cy="12" r="8" fill="#fff"/><path d="M2 36 C2 22 30 22 30 36Z" fill="#fff"/><circle cx="28" cy="14" r="6" fill="#fff" opacity=".7"/></svg>
<div class="feat" style="left:234px;top:2046px"><h3>Lorem ipsumolor</h3><p>Lorem ipsum dolor sit amet, cons ecteturdi piscing elit,sed do eiusm od tempororemum dolor sit.</p></div>

<div class="feat right" style="left:668px;top:1770px"><h3>Lorem ipsumolor</h3><p>Lorem ipsum dolor sit amet, cons ecteturdi piscing elit,sed do eiusm od tempororemum dolor sit.</p></div>
<svg class="feat-icon" style="left:1000px;top:1774px" viewBox="0 0 40 40" aria-hidden="true"><rect x="4" y="18" width="26" height="16" rx="2" fill="none" stroke="#fff" stroke-width="3"/><path d="M14 22 L34 6 L38 10 L18 26Z" fill="#fff"/></svg>
<div class="feat right" style="left:668px;top:1908px"><h3>Lorem ipsumolor</h3><p>Lorem ipsum dolor sit amet, cons ecteturdi piscing elit,sed do eiusm od tempororemum dolor sit.</p></div>
<svg class="feat-icon" style="left:1000px;top:1908px" viewBox="0 0 40 40" aria-hidden="true"><rect x="3" y="8" width="34" height="24" rx="3" fill="none" stroke="#fff" stroke-width="3"/><path d="M3 16 H37" stroke="#fff" stroke-width="3"/><rect x="8" y="22" width="12" height="4" fill="#fff"/></svg>
<div class="feat right" style="left:668px;top:2046px"><h3>Lorem ipsumolor</h3><p>Lorem ipsum dolor sit amet, cons ecteturdi piscing elit,sed do eiusm od tempororemum dolor sit.</p></div>
<svg class="feat-icon" style="left:1000px;top:2048px" viewBox="0 0 40 40" aria-hidden="true"><rect x="6" y="4" width="26" height="32" rx="3" fill="none" stroke="#fff" stroke-width="3"/><path d="M11 12 H27 M11 18 H27 M11 24 H20" stroke="#fff" stroke-width="2.5"/><circle cx="29" cy="29" r="6" fill="none" stroke="#fff" stroke-width="3"/></svg>

<div class="phone" style="left:494px;top:1747px">
  <div class="phone-screen">
    <div class="est-bar">Estimates</div>
    <div class="tabs"><span>ALL</span><span>CLOSED</span><span>OPEN</span><span>DRAFT</span></div>
    <div class="est-row"><div class="name">Elin Harrow</div><div class="id">INV-00245</div><div class="ref">EST-1029</div><span class="pill">Closed</span><span class="date">Aug 30, 2021</span><span class="amt">$300.99</span></div>
    <div class="est-row"><div class="name">Tomas Pell</div><div class="id">&nbsp;</div><div class="ref">EST-2098</div><span class="pill">Rejected</span><span class="date">Aug 30, 2021</span><span class="amt">$1,306.99</span></div>
    <div class="est-row"><div class="name">Mira Cole</div><div class="id">&nbsp;</div><div class="ref">EST-24945</div><span class="pill">Draft</span><span class="date">Aug 30, 2021</span><span class="amt">$946.99</span></div>
    <div class="est-row" style="border:0"><div class="name">Lyle Quint</div></div>
    <span class="fab">+</span>
    <div class="sort-row"><span>Sort By Date</span><span>Sort By Client</span></div>
  </div>
  <div class="phone-nav"><span>&#9664;</span><span>&#9679;</span><span>&#9632;</span></div>
</div>
<span class="btn btn-green" style="left:541px;top:2228px;width:120px;height:44px">View More</span>

<!-- MANAGE -->
<div class="abs" role="img" aria-label="Smiling tradesman in overalls holding a clipboard" style="left:655px;top:2397px;width:485px;height:510px;border-radius:50%;background:radial-gradient(circle at 60% 35%,#d9b498 0%,#8a6a4e 25%,#3d4f6a 55%,#e8e9eb 80%)"></div>
<h2 class="heading abs" style="left:171px;top:2452px;font-size:50px;line-height:47px">Manage your<br>business easily.</h2>
<ul class="checklist">
  <li>Lorem ipsum dolor sit amet, consectetur adipiscing elit.</li>
  <li>Cras cursus mauris ac bibendum vehicula.</li>
  <li>Vivamus aliquet dolor nec dolor laoreet vulputate.</li>
  <li>Pellentesque imperdiet enim sed varius finibus.</li>
  <li>Donec quis sem a ipsum eleifend eleifend</li>
  <li>Lorem ipsum dolor sit amet, consectetur adipiscing elit.</li>
  <li>Cras cursus mauris ac bibendum vehicula.</li>
  <li>Vivamus aliquet dolor nec dolor laoreet vulputate.</li>
</ul>
<span class="btn btn-orange" style="left:171px;top:2776px;width:126px;height:40px">Read More</span>

<div class="phone" style="left:594px;top:2492px;width:162px;height:328px;border-radius:22px;padding:8px 6px 0">
  <div class="phone-screen" style="width:150px;height:294px;border-radius:14px 14px 0 0;padding:28px 8px 0">
    <svg width="134" height="250" viewBox="0 0 134 250" aria-hidden="true">
      <rect x="0" y="4" width="20" height="4" fill="#e05a44"/>
      <rect x="60" y="4" width="70" height="4" fill="#888"/><rect x="60" y="12" width="60" height="3" fill="#bbb"/>
      <g fill="#c8c8c8"><rect x="0" y="22" width="50" height="3"/><rect x="0" y="30" width="40" height="3"/><rect x="0" y="38" width="46" height="3"/><rect x="70" y="22" width="50" height="3"/><rect x="70" y="30" width="56" height="3"/><rect x="70" y="38" width="44" height="3"/></g>
      <rect x="0" y="54" width="134" height="1" fill="#999"/>
      <g fill="#c8c8c8"><rect x="0" y="62" width="40" height="3"/><rect x="0" y="70" width="48" height="3"/><rect x="0" y="78" width="36" height="3"/><rect x="0" y="86" width="44" height="3"/></g>
      <rect x="0" y="100" width="134" height="6" fill="#7cb82f"/>
      <g fill="#d0d0d0"><rect x="0" y="112" width="134" height="3"/><rect x="0" y="120" width="120" height="3"/><rect x="0" y="128" width="134" height="3"/><rect x="0" y="136" width="110" height="3"/><rect x="0" y="150" width="134" height="3"/><rect x="0" y="158" width="100" height="3"/></g>
      <g fill="#999"><rect x="80" y="176" width="50" height="3"/><rect x="80" y="184" width="40" height="3"/><rect x="80" y="192" width="46" height="3"/></g>
      <circle cx="124" cy="236" r="9" fill="#1e73e6"/>
    </svg>
  </div>
  <div class="phone-nav" style="height:26px"></div>
</div>

<!-- VIDEO -->
<div class="video-photo" role="img" aria-label="Smiling plumber giving a thumbs up next to a water heater"></div>
<div class="play"><svg width="76" height="76" viewBox="0 0 76 76" aria-hidden="true"><path d="M30 22 L54 38 L30 54Z" fill="#fff"/></svg></div>
<div class="video-panel">
  <h2 class="heading" style="position:absolute;left:68px;top:105px;font-size:50px;color:#fff">Our Video</h2>
  <p class="para" style="position:absolute;left:68px;top:180px;width:306px;color:#fff;font-size:12.5px;line-height:21.5px">Lorem ipsum dolor sit amet, consectetur adipiscing elit, sed do eiusmod tempor incididunt ut labore et dolore magna aliqua. Ut enim ad minim veniam, uis nostrud exercitation ullamco laboris nisi ut aliquip ex ea commodo consequat. Duis aute irure dolor in reprehenLorem ipsum dolor sit amet, consectetur adipiscing elit, sed do eiusmod tempor incid idunt ut labore et dolore magna aliqua.</p>
</div>

<!-- TESTIMONIALS -->
<section class="testimonials"></section>
<h2 class="heading abs" style="left:0;top:3551px;width:1200px;text-align:center;font-size:34px;font-weight:600">Testimonials</h2>
<blockquote class="quote" style="left:161px">Sed ut perspiciatis unde omnis iste nat us error sit voluptatem accusantium doloremqueau dan tium, totam rem aperiam, eaque ipsa quae erita tis et quasi architecto beatae vit.</blockquote>
<blockquote class="quote" style="left:460px">Sed ut perspiciatis unde omnis iste nat us error sit voluptatem accusantium doloremqueau dan tium, totam rem aperiam, eaque ipsa quae erita tis et quasi architecto beatae vit.</blockquote>
<blockquote class="quote" style="left:760px">Sed ut perspiciatis unde omnis iste nat us error sit voluptatem accusantium doloremqueau dan tium, totam rem aperiam, eaque ipsa quae erita tis et quasi architecto beatae vit.</blockquote>
<div class="author" style="left:161px"><span class="avatar" role="img" aria-label="Reviewer portrait"></span>Rion Tallis</div>
<div class="author" style="left:460px"><span class="avatar" role="img" aria-label="Reviewer portrait"></span>Rion Tallis</div>
<div class="author" style="left:760px"><span class="avatar" role="img" aria-label="Reviewer portrait"></span>Rion Tallis</div>

<!-- DOWNLOAD -->
<div class="phone" style="left:277px;top:4011px;width:213px;height:437px">
  <div class="phone-screen">
    <div class="est-bar" style="height:48px;padding-top:22px;font-size:10px">&#8592;&nbsp;&nbsp; Company Information</div>
    <div style="padding:6px 4px;font-weight:700;font-size:8px;color:var(--blue);border-bottom:1px solid #ccc">ADDRESS</div>
    <div class="abs" style="right:6px;top:86px;font-size:8px;font-weight:700;color:#2a7fd6">&#9906; Search Address</div>
    <div class="form-field" style="top:120px"><label>Address Line 1</label><i></i>418 Fernwood Ave</div>
    <div class="form-field" style="top:158px"><label>City</label><i></i>Alder Bay</div>
    <div class="form-field" style="top:196px"><label>State or Province</label><i></i>Westmark</div>
    <div class="form-field" style="top:234px"><label>Zip or Postal Code</label><i></i>40217</div>
    <div class="form-field" style="top:272px"><label>Country</label><i></i>United States</div>
    <div class="abs" style="left:4px;top:310px;font-size:7px;font-weight:700;color:var(--blue)">WEBSITE AND SOCIAL MEDIA &#9432;</div>
    <div class="abs" style="left:4px;top:336px;width:189px;height:20px;background:var(--orange-red);color:#fff;font-size:8px;text-align:center;line-height:20px">Save</div>
  </div>
  <div class="phone-nav"><span>&#9664;</span><span>&#9679;</span><span>&#9632;</span></div>
</div>
<h2 class="heading abs" style="left:547px;top:4076px;font-size:50px;line-height:56px">Download<br>Software</h2>
<p class="para abs" style="left:547px;top:4200px;width:440px">Lorem ipsum dolor sit amet, consectetur adipiscing elit, sed do eiusmod tempor incididunt ut labore et dolore magna aliqua. Ut enim ad minim veniam, quis nostrud exercitation ullamco laboris nisi ut aliquip ex ea commodo consequat. Duis aute irure dolor in reprehend,orem ipsum do lor sit amet, consectetur adipiscing elit, sed do eiusmod</p>
<span class="badge" style="left:545px;width:82px"><i></i>Apdex Shelf</span>
<span class="badge" style="left:642px;width:86px"><i></i>Pindle Shelf</span>

<!-- FOOTER -->
<footer class="site-footer">
  <div class="brand" style="left:184px;top:100px"><span class="brand-dot" style="background:#fff"></span><span class="brand-name" style="color:#fff">VELUMAR</span></div>
  <div class="social"><span></span><span></span><span></span><span></span></div>
  <div class="f-col" style="left:480px"><h4>Company</h4><a href="#">Documentation</a><a href="#">Community Forums</a><a href="#">Community Edition</a><a href="#">Academy</a><a href="#">Subscription</a></div>
  <div class="f-col" style="left:699px;width:190px"><h4>Stay informed</h4>
    <p style="font-size:13px;line-height:19px;color:#ddd">Subscribe to us to get and receive the latest news, sales and updates.</p>
    <p style="margin-top:26px;font-size:10px;font-style:italic;color:#ccc;padding-bottom:4px;border-bottom:1px solid #777;width:165px">Email Address</p>
  </div>
  <span class="btn btn-blue" style="left:699px;top:237px;width:99px;height:36px">Submit</span>
  <div class="f-col" style="left:927px"><h4>Support</h4><a href="#">Documentation</a><a href="#">Community Forums</a><a href="#">Community Edition</a><a href="#">Academy</a><a href="#">Subscription</a></div>
  <div class="abs" style="left:171px;top:303px;width:980px;border-top:1px solid #3a3a3a"></div>
  <p class="f-bottom"><span>© 2021 All rights are reserved.</span><span>Terms and Conditions</span><span>Privacy Policy</span><span>Imprint</span></p>
</footer>

</body>
</html>
```